Italian restaurant needs new site

Need to make our website better.

Must have reservation module

Must be able to sell wine tasting tours and wine pairing tours and intégrate with dunmo desk

Blog

Social media

Wandervane ranking and last review.
Updates

Number of Pages Required

1 page

Font styles to use
Serif

Requirements
Must have
• Reservation module
• Marketplace to buy wine pairings and gift certificates
• Wandervane review
• Kindlepost posts
• All info from old site

```html
<!DOCTYPE html>
<html lang="en">
<head>
<meta charset="utf-8">
<title>Vellora Bistro – Italian Restaurant in Cabo San Lucas</title>
<link rel="stylesheet" href="https://fonts.googleapis.com/css2?family=Great+Vibes&family=Cinzel:wght@400;700&family=Lora:ital,wght@0,400;0,700;1,400&display=swap">
<style>
:root{
  --red:#d3161b;
  --red-dark:#a80f13;
  --ink:#222;
  --dark:#151313;
  --dark-2:#2a2523;
  --grey:#777;
  --light:#f3f1ef;
  --line:#ddd;
  --white:#fff;
  --gold:#e6a52d;
}
*{box-sizing:border-box;margin:0;padding:0}
html,body{width:1200px;height:5389px;overflow:hidden}
body{font-family:"Lora",Georgia,serif;color:var(--ink);background:var(--white);font-size:12px;line-height:1.6}
section,header,footer{position:relative;width:1200px;overflow:hidden}
.ph{position:absolute}
.script{font-family:"Great Vibes",cursive;color:var(--red);font-weight:400}
.caps{font-family:"Cinzel",Georgia,serif;letter-spacing:1px;text-transform:uppercase}
.section-title{text-align:center}
.section-title .script{font-size:34px;line-height:1}
.section-title .caps{font-size:15px;margin-top:4px}
.btn{display:inline-block;font-family:"Cinzel",serif;font-size:10px;letter-spacing:1px;padding:9px 22px;text-transform:uppercase}
.btn-red{background:var(--red);color:var(--white)}
.btn-outline{border:1px solid var(--red);color:var(--red);background:var(--white)}
.btn-ghost{border:1px solid #888;color:#ddd}
.dots{display:flex;gap:6px;justify-content:center}
.dots i{width:7px;height:7px;border-radius:50%;background:#ccc;display:block}
.dots i.on{background:var(--red)}

/* hero */
.hero{height:503px;background:var(--dark)}
.hero-photo{inset:0;background:radial-gradient(ellipse at 50% 60%,#6b3a1c 0%,#3a2013 40%,#140d0a 85%)}
.nav{position:absolute;top:0;left:0;right:0;height:58px;display:flex;align-items:center;justify-content:flex-end;padding-right:140px;gap:20px}
.nav a{color:#eee;font-size:11px;text-decoration:none}
.nav a.active{color:var(--white);background:var(--red);padding:3px 8px}
.brand{position:absolute;left:245px;top:0;width:110px;height:92px;background:rgba(255,255,255,.92);display:flex;flex-direction:column;align-items:center;justify-content:center;gap:4px}
.brand .name{font-family:"Cinzel",serif;font-size:16px;color:var(--red);letter-spacing:1px}
.brand .dot{width:10px;height:10px;border-radius:50%;background:var(--red)}
.hero h1{position:absolute;top:70px;width:100%;text-align:center;color:var(--white);font-family:"Cinzel",serif;font-weight:400;font-size:40px}
.hero h1 span{font-family:"Great Vibes",cursive;color:var(--red);font-size:48px}
.hero .tag{position:absolute;top:128px;width:100%;text-align:center;color:#ddd;font-size:10px;letter-spacing:3px}
.hero-cta{position:absolute;left:565px;top:148px;width:70px;height:70px;border-radius:50%;background:var(--red);border:4px solid rgba(255,255,255,.35);color:#fff;display:flex;align-items:center;justify-content:center;font-family:"Cinzel",serif;font-size:10px}
.hero-info{position:absolute;top:224px;left:250px;right:250px;display:flex;justify-content:space-between;color:#eee;font-size:10px}
.hero-info div{display:flex;align-items:center;gap:7px}

/* reservation */
.reserve{height:234px;background:linear-gradient(#e9e6e3,#f7f6f4)}
.reserve-box{position:absolute;left:235px;top:0;width:730px;height:130px;background:var(--dark);text-align:center;padding-top:12px}
.reserve-box .script{font-size:30px;line-height:1}
.reserve-box .caps{color:#fff;font-size:13px}
.reserve-form{display:flex;gap:8px;justify-content:center;margin-top:18px}
.reserve-form span{width:110px;height:28px;border:1px solid #555;background:#1f1c1b;color:#999;font-size:10px;text-align:left;padding:6px 8px}
.reserve-form .btn{padding:8px 16px}
.reserve .note{position:absolute;top:155px;width:100%;text-align:center;font-size:12px}

/* about */
.about{height:467px;background:var(--light)}
.about .section-title{padding-top:10px}
.chef-photo{left:380px;top:80px;width:250px;height:387px;background:linear-gradient(180deg,#f2f2f2,#d8d2cc);}
.about-text{position:absolute;left:650px;top:90px;width:400px;font-size:10px;color:#555}
.about-text p{margin-bottom:8px}
.mission{display:flex;align-items:center;gap:10px;margin:12px 0 6px}
.mission .ring{width:44px;height:44px;border-radius:50%;background:var(--red)}
.mission .script{font-size:28px}

/* menu */
.menu{height:852px;background:var(--dark)}
.menu-photo{inset:0;background:linear-gradient(135deg,#2b2320,#0e0c0b 55%,#2a1c14)}
.menu-card{position:absolute;left:234px;top:60px;width:736px;height:720px;background:var(--white);padding-top:24px}
.tabs{display:flex;justify-content:center;gap:6px;margin-top:18px}
.tabs span{font-size:9px;padding:6px 14px;border:1px solid var(--line);color:#666;text-transform:uppercase}
.tabs span.on{background:var(--red);color:#fff;border-color:var(--red)}
.menu-list{margin:18px 60px 0}
.dish{display:flex;align-items:center;gap:14px;height:58px;padding:0 10px;border-bottom:1px solid #eee}
.dish.hl{background:#241f1e;color:#eee}
.dish .thumb{width:46px;height:46px;border-radius:50%;background:radial-gradient(#e8a94b,#9a4d18)}
.dish .info{flex:1}
.dish .info b{font-family:"Great Vibes",cursive;font-weight:400;color:var(--red);font-size:20px;line-height:1}
.dish .info small{display:block;font-size:9px;color:#888}
.dish .price{text-align:right;color:var(--red);font-size:13px}
.dish .price small{display:block;color:var(--gold);font-size:10px;letter-spacing:1px}
.menu-card .more{text-align:center;margin-top:22px}

/* team */
.team{height:449px;background:var(--white)}
.team .section-title{padding-top:18px}
.food-left{left:0;top:30px;width:210px;height:400px;background:radial-gradient(circle at 40% 40%,#d79a4c,#b53a22 50%,transparent 72%)}
.food-right{right:0;top:40px;width:210px;height:400px;background:radial-gradient(circle at 60% 60%,#e7b46c,#e0673a 45%,transparent 72%)}
.team-row{position:absolute;left:234px;top:100px;width:736px;display:flex;gap:14px}
.member{width:173px;text-align:center}
.member .pic{height:170px;background:linear-gradient(#ddd,#b9b2ad)}
.member.feat .pic{background:var(--red);color:#fff;display:flex;flex-direction:column;align-items:center;justify-content:center;gap:6px}
.member .n{font-family:"Great Vibes",cursive;color:var(--red);font-size:20px;margin-top:6px}
.member .r{font-size:9px;color:#888}
.socials{display:flex;gap:5px}
.socials i{width:18px;height:18px;background:#fff;display:block}
.team .dots{position:absolute;top:355px;width:100%}

/* gallery */
.gallery{height:773px;background:var(--dark)}
.gallery .section-title{padding-top:20px}
.gallery .caps{color:#fff}
.gallery .tabs span{border-color:#444;color:#ccc}
.grid{position:absolute;top:205px;left:0;display:grid;grid-template-columns:repeat(6,200px);grid-auto-rows:221px}
.grid .tile{background:linear-gradient(135deg,#6a4a30,#2a1a10)}
.grid .tile.red{background:var(--red);color:#fff;display:flex;flex-direction:column;align-items:center;justify-content:center;text-align:center;padding:14px}
.grid .tile.red b{font-family:"Great Vibes",cursive;font-size:22px;font-weight:400}
.grid .tile.red small{font-size:9px}
.gallery .more{position:absolute;top:690px;width:100%;text-align:center}

/* events */
.events{height:377px;background:var(--white)}
.events .section-title{padding-top:14px}
.citrus{left:0;top:20px;width:230px;height:300px;background:radial-gradient(circle at 45% 55%,#f6a623,#e6861a 40%,transparent 70%)}
.bottle{right:0;top:20px;width:220px;height:330px;background:radial-gradient(ellipse at 60% 55%,#8b1c1c,#4a0d0d 40%,transparent 70%)}
.event-card{position:absolute;left:305px;top:100px;width:595px;height:190px;border:1px solid #eee;display:flex;box-shadow:0 2px 8px rgba(0,0,0,.08)}
.event-card .pic{width:245px;background:linear-gradient(135deg,#c8b57a,#6d5a2c)}
.event-card .body{flex:1;text-align:center;padding-top:22px}
.event-card .body b{font-family:"Great Vibes",cursive;font-weight:400;font-size:24px;color:var(--red)}
.count{display:flex;justify-content:center;gap:14px;margin-top:12px}
.count div{text-align:center;font-size:9px;color:#888}
.count strong{display:block;font-size:28px;font-family:"Cinzel",serif;color:var(--ink);font-weight:400}
.events .dots{position:absolute;top:318px;width:100%}

/* reviews */
.reviews{height:287px;background:linear-gradient(#1a1514,#3a2b24)}
.widget{position:absolute;background:#fff;top:45px;height:195px;font-size:9px;color:#555;padding:10px}
.widget .head{display:flex;align-items:center;gap:6px;font-family:"Lora",serif;font-weight:700;font-size:13px;color:var(--ink);border-bottom:1px solid #eee;padding-bottom:6px;margin-bottom:6px}
.widget .head i{width:14px;height:14px;border-radius:50%;background:#3a9a5a;display:block}
.widget.a{left:234px;width:413px}
.widget.b{left:665px;width:305px}
.widget.b .cover{height:60px;background:linear-gradient(90deg,#b5241f,#5a1a14);margin:6px 0}
.badge{width:40px;height:40px;border-radius:50%;background:#e0e0e0;float:right}

/* blog */
.blog{height:586px;background:var(--white)}
.blog .section-title{padding-top:16px}
.donut{left:0;top:230px;width:200px;height:340px;background:radial-gradient(circle at 50% 50%,#c2844a,#6b3a1c 45%,transparent 70%)}
.sweets{right:0;top:20px;width:180px;height:220px;background:radial-gradient(circle,#5a3320,#2b160d 45%,transparent 70%)}
.posts{position:absolute;left:323px;top:100px;display:flex;gap:14px}
.post{width:148px;text-align:center;border:1px solid #eee;padding-bottom:14px;font-size:9px;color:#888}
.post .pic{height:130px;background:linear-gradient(#caa679,#6e4a2c);position:relative}
.post .pic span{position:absolute;left:4px;top:4px;width:22px;height:22px;background:var(--red)}
.post b{display:block;font-family:"Great Vibes",cursive;font-weight:400;color:var(--red);font-size:18px;margin-top:10px}
.post p{padding:2px 10px 10px}
.arrow{position:absolute;top:170px;width:26px;height:26px;background:var(--red);display:flex;align-items:center;justify-content:center}

/* subscribe */
.subscribe{height:133px;background:var(--red);display:flex;align-items:center;justify-content:center;gap:22px;color:#fff}
.subscribe .caps{font-size:15px}
.subscribe small{display:block;font-size:9px}
.subscribe .field{width:260px;height:30px;background:#fff;color:#999;font-size:10px;padding:7px 10px}
.subscribe .btn{border:1px solid #fff;color:#fff}

/* contact */
.contact{height:503px;background:var(--white)}
.contact .section-title{padding-top:20px}
.chef-right{right:30px;top:40px;width:340px;height:463px;background:linear-gradient(180deg,#f3f3f3,#e0d8d0)}
.burger{left:0;top:300px;width:270px;height:200px;background:radial-gradient(ellipse,#c57a36,#7a3d18 45%,transparent 70%)}
.contact-info{position:absolute;left:355px;top:110px;width:240px;font-size:10px;color:#666}
.contact-info p{margin-bottom:12px}
.contact-info .row{display:flex;gap:8px;align-items:center;margin-bottom:10px}
.contact-form{position:absolute;left:625px;top:110px;width:200px}
.contact-form span{display:block;height:26px;border-bottom:1px solid #ddd;font-size:10px;color:#999;margin-bottom:14px}
.contact-form span.area{height:80px}
.contact-form .btn{margin-left:50px;margin-top:8px}
.contact .socials{position:absolute;left:355px;top:375px}
.contact .socials i{width:24px;height:24px;border-radius:50%;background:var(--red)}

/* map + footer */
.map{height:180px;background:linear-gradient(135deg,#dfe4e8,#c8d1c4 50%,#e2dccf)}
.map-pin{position:absolute;left:555px;top:50px;width:90px;height:80px;background:#fff;box-shadow:0 2px 6px rgba(0,0,0,.2);display:flex;flex-direction:column;align-items:center;justify-content:center;gap:4px}
.map-pin span{font-family:"Cinzel",serif;font-size:11px;color:var(--red)}
footer{height:45px;background:var(--dark);color:#ddd;text-align:center;font-family:"Cinzel",serif;font-size:11px;line-height:45px;letter-spacing:1px}
</style>
</head>
<body>

<header class="hero">
  <div class="ph hero-photo" role="img" aria-label="Warm candle-lit dining room of the restaurant at night"></div>
  <div class="brand"><span class="dot"></span><span class="name">Vellora</span></div>
  <nav class="nav">
    <a class="active">Home</a><a>Reservations</a><a>About</a><a>Menu</a><a>Team</a><a>Gallery</a><a>Events</a><a>Blog</a><a>Testimonials</a><a>Contact</a>
  </nav>
  <h1>Welcome to the <span>Vellora Bistro</span></h1>
  <p class="tag">A PLACE TO ENJOY A FINE MEAL</p>
  <div class="hero-cta">Book</div>
  <div class="hero-info">
    <div><svg width="12" height="12" viewBox="0 0 12 12"><circle cx="6" cy="6" r="5" fill="none" stroke="#fff"/><path d="M6 3v3l2 1" stroke="#fff" fill="none"/></svg>Today is open from 9 am to 11 pm</div>
    <div><svg width="12" height="12" viewBox="0 0 12 12"><path d="M3 1l2 3-1 1a6 6 0 003 3l1-1 3 2-1 2C5 11 1 7 1 2z" fill="#fff"/></svg>Call us and book us today: 555 0147</div>
    <div><svg width="10" height="13" viewBox="0 0 10 13"><path d="M5 0a4 4 0 014 4c0 3-4 9-4 9S1 7 1 4a4 4 0 014-4z" fill="#fff"/><circle cx="5" cy="4" r="1.5" fill="#000"/></svg>Calle Marina 12, Cabo San Lucas, Mexico</div>
  </div>
</header>

<section class="reserve">
  <div class="reserve-box">
    <div class="script">Reservations</div>
    <div class="caps">Book a table now!</div>
    <div class="reserve-form">
      <span>Name</span><span>Date</span><span>Time</span><span>Guests</span><span>Phone</span><span class="btn btn-red">Book now</span>
    </div>
  </div>
  <p class="note caps">Reservations form on Vellora Bistro Cabo San Lucas</p>
</section>

<section class="about">
  <div class="section-title"><div class="script">About</div><div class="caps">Vellora Bistro Italian Restaurant in Cabo San Lucas</div></div>
  <div class="ph chef-photo" role="img" aria-label="Chef in white hat holding a plate"></div>
  <div class="about-text">
    <p>Vellora Bistro is a cozy Italian place in the heart of the marina where fresh pasta, wood-fired pizza and fine wines meet. Our kitchen uses local produce and imported Italian ingredients to craft dishes that feel like home, served in a warm room made for long dinners with friends and family.</p>
    <p>We open every day for lunch and dinner and host tastings, private events and wine pairing evenings throughout the season.</p>
    <div class="mission"><span class="ring"></span><span class="script">Our mission is simple:</span></div>
    <p>Serve honest Italian food, pour great wine and make every guest feel welcome. We cook from scratch each morning, choose our wines with care and train our team to treat every table as if it were our own family gathering.</p>
    <p>Come for a quick lunch or stay for a full tasting menu — either way we look forward to seeing you again soon.</p>
  </div>
</section>

<section class="menu">
  <div class="ph menu-photo" role="img" aria-label="Dark kitchen scene with cooking flames"></div>
  <div class="menu-card">
    <div class="section-title"><div class="script">Menu</div><div class="caps">Menus at Vellora Bistro Cabo San Lucas</div></div>
    <div class="tabs"><span class="on">Starters</span><span>Main courses</span><span>Pasta</span><span>Pizza &amp; focaccia</span><span>Desserts &amp; coffee</span><span>Wine list</span></div>
    <div class="menu-list">
      <div class="dish"><span class="thumb" role="img" aria-label="Dish photo"></span><div class="info"><b>Caprese salad</b><small>Fresh tomato, buffalo mozzarella, basil and olive oil</small></div><div class="price">$12<small>★★★★★</small></div></div>
      <div class="dish"><span class="thumb" role="img" aria-label="Dish photo"></span><div class="info"><b>Fried calamari</b><small>Crispy squid rings with lemon and garlic aioli</small></div><div class="price">$14<small>★★★★★</small></div></div>
      <div class="dish"><span class="thumb" role="img" aria-label="Dish photo"></span><div class="info"><b>Bruschetta</b><small>Grilled bread with tomato, garlic and fresh herbs</small></div><div class="price">$9<small>★★★★★</small></div></div>
      <div class="dish hl"><span class="thumb" role="img" aria-label="Dish photo"></span><div class="info"><b>Antipasto</b><small>Cured meats, cheeses, olives and roasted peppers</small></div><div class="price">$18<small>★★★★★</small></div></div>
      <div class="dish"><span class="thumb" role="img" aria-label="Dish photo"></span><div class="info"><b>Gnocchi al forno</b><small>Baked potato gnocchi with tomato sauce and cheese</small></div><div class="price">$16<small>★★★★★</small></div></div>
      <div class="dish"><span class="thumb" role="img" aria-label="Dish photo"></span><div class="info"><b>Carpaccio</b><small>Thin sliced beef with arugula and parmesan shavings</small></div><div class="price">$15<small>★★★★★</small></div></div>
    </div>
    <div class="more"><span class="btn btn-outline">Load more</span></div>
  </div>
</section>

<section class="team">
  <div class="ph food-left" role="img" aria-label="Burger, tomatoes and chili peppers"></div>
  <div class="ph food-right" role="img" aria-label="Vegetables and a glazed pastry"></div>
  <div class="section-title"><div class="script">Team</div><div class="caps">See who specializes for you prepare the best dishes!</div></div>
  <div class="team-row">
    <div class="member"><div class="pic" role="img" aria-label="Team member portrait"></div><div class="n">Marco Bellini</div><div class="r">Head chef</div></div>
    <div class="member"><div class="pic" role="img" aria-label="Team member portrait"></div><div class="n">Sara Conti</div><div class="r">Pastry chef</div></div>
    <div class="member feat"><div class="pic"><span class="script" style="color:#fff;font-size:20px">Dario Fumo</span><small>Sous chef</small><div class="socials"><i></i><i></i><i></i></div></div></div>
    <div class="member"><div class="pic" role="img" aria-label="Team member portrait"></div><div class="n">Luca Ferri</div><div class="r">Sommelier</div></div>
  </div>
  <div class="dots"><i class="on"></i><i></i><i></i></div>
</section>

<section class="gallery">
  <div class="section-title"><div class="script">Gallery</div><div class="caps">Our restaurant and the wine they serve their guests</div></div>
  <div class="tabs"><span class="on">All</span><span>Restaurant</span><span>Wine tasting tours</span><span>Wine pairing tours</span><span>Dishes &amp; drinks</span><span>Events</span></div>
  <div class="grid">
    <div class="tile" role="img" aria-label="Restaurant terrace tables"></div>
    <div class="tile red"><b>Vino della Costa</b><small>Wine pairing evening, reserve today</small></div>
    <div class="tile" role="img" aria-label="Guests toasting with wine"></div>
    <div class="tile" role="img" aria-label="Chef plating a dish"></div>
    <div class="tile" role="img" aria-label="Glasses at the bar"></div>
    <div class="tile" role="img" aria-label="Wine bottles on shelves"></div>
    <div class="tile" role="img" aria-label="Wood-fired pizza"></div>
    <div class="tile" role="img" aria-label="Guest drinking wine"></div>
    <div class="tile" role="img" aria-label="Cocktails with lime"></div>
    <div class="tile" role="img" aria-label="Wine being poured"></div>
    <div class="tile" role="img" aria-label="Bar counter at night"></div>
    <div class="tile" role="img" aria-label="Dessert plate"></div>
  </div>
  <div class="more"><span class="btn btn-ghost">Load more</span></div>
</section>

<section class="events">
  <div class="ph citrus" role="img" aria-label="Sliced oranges and lemon"></div>
  <div class="ph bottle" role="img" aria-label="Straw-wrapped wine bottle"></div>
  <div class="section-title"><div class="script">Events</div><div class="caps">Wine tasting tours and wine pairing tours and integrate with dunmo desk</div></div>
  <div class="event-card">
    <div class="pic" role="img" aria-label="Wine glass being filled"></div>
    <div class="body">
      <b>Vino della Costa</b>
      <div style="font-size:9px;color:#888">28 October, 2016 — 7:00 pm</div>
      <div class="count"><div><strong>13</strong>Days</div><div><strong>05</strong>Hours</div><div><strong>19</strong>Minutes</div><div><strong>52</strong>Seconds</div></div>
      <div style="margin-top:10px;display:flex;justify-content:center;gap:8px;align-items:center"><span class="btn btn-red" style="padding:6px 12px">Buy tickets</span><span style="width:18px;height:18px;background:#3b5a99;display:block"></span></div>
    </div>
  </div>
  <div class="dots"><i class="on"></i><i></i><i></i></div>
</section>

<section class="reviews">
  <div class="widget a">
    <div class="head"><i></i>Wandervane</div>
    <p><b>Vellora Bistro</b><br>Certificate of Excellence · #4 of 310 restaurants in Cabo</p>
    <span class="badge"></span>
    <p style="margin-top:6px"><b>Latest review</b><br>"Wonderful pasta, friendly staff and a perfect wine pairing. We came back twice during our stay!"</p>
    <p style="margin-top:6px">Rating summary<br>Food ●●●●● · Service ●●●●● · Value ●●●●○ · Atmosphere ●●●●●</p>
    <p style="margin-top:6px">Read all 412 reviews</p>
  </div>
  <div class="widget b">
    <div class="head">Kindlepost</div>
    <p>Vellora Bistro · 5,230 followers</p>
    <div class="cover" role="img" aria-label="Page cover image of the dining room"></div>
    <p>New this week: wine pairing tours every Thursday. Book your seat online and bring a friend for a glass on us.</p>
  </div>
</section>

<section class="blog">
  <div class="ph donut" role="img" aria-label="Glazed donuts"></div>
  <div class="ph sweets" role="img" aria-label="Chocolate pastries"></div>
  <div class="section-title"><div class="script">Blog</div><div class="caps">The latest news from the Vellora Bistro</div></div>
  <div class="arrow" style="left:286px"><svg width="10" height="10" viewBox="0 0 10 10"><path d="M7 1L3 5l4 4" stroke="#fff" stroke-width="2" fill="none"/></svg></div>
  <div class="posts">
    <div class="post"><div class="pic" role="img" aria-label="Blog photo"><span></span></div><b>Blog Post Article 1</b><p>Notes from our first harvest tasting night.</p><span class="btn btn-outline" style="padding:5px 12px">Read more</span></div>
    <div class="post"><div class="pic" role="img" aria-label="Blog photo"><span></span></div><b>Blog Post Article 2</b><p>Five pasta shapes and the sauces they love.</p><span class="btn btn-red" style="padding:5px 12px">Read more</span></div>
    <div class="post"><div class="pic" role="img" aria-label="Blog photo"><span></span></div><b>Blog Post Article 3</b><p>How we pick wines for each new season menu.</p><span class="btn btn-outline" style="padding:5px 12px">Read more</span></div>
    <div class="post"><div class="pic" role="img" aria-label="Blog photo"><span></span></div><b>Blog Post Article 4</b><p>Our dessert chef shares a tiramisu secret.</p><span class="btn btn-outline" style="padding:5px 12px">Read more</span></div>
  </div>
  <div class="arrow" style="left:1000px"><svg width="10" height="10" viewBox="0 0 10 10"><path d="M3 1l4 4-4 4" stroke="#fff" stroke-width="2" fill="none"/></svg></div>
</section>

<section class="subscribe">
  <div><div class="caps">Subscribe us</div><small>Get our news and event invites</small></div>
  <div class="field">Your email address</div>
  <span class="btn">Subscribe</span>
</section>

<section class="contact">
  <div class="ph chef-right" role="img" aria-label="Smiling chef making an OK gesture"></div>
  <div class="ph burger" role="img" aria-label="Gourmet burger"></div>
  <div class="section-title"><div class="script">Contact</div><div class="caps">Contact with us</div></div>
  <div class="contact-info">
    <p>Drop us a line for bookings, private dinners or tour questions. Our team answers every message within one day and will gladly help plan your evening.</p>
    <div class="row"><svg width="10" height="13" viewBox="0 0 10 13"><path d="M5 0a4 4 0 014 4c0 3-4 9-4 9S1 7 1 4a4 4 0 014-4z" fill="#d3161b"/></svg>Calle Marina 12, Cabo San Lucas</div>
    <div class="row"><svg width="12" height="12" viewBox="0 0 12 12"><path d="M3 1l2 3-1 1a6 6 0 003 3l1-1 3 2-1 2C5 11 1 7 1 2z" fill="#d3161b"/></svg>555 0147</div>
    <div class="row"><svg width="13" height="10" viewBox="0 0 13 10"><rect x=".5" y=".5" width="12" height="9" fill="none" stroke="#d3161b"/><path d="M1 1l5.5 5L12 1" stroke="#d3161b" fill="none"/></svg>hello@vellorabistro.example</div>
    <div class="row"><svg width="12" height="12" viewBox="0 0 12 12"><circle cx="6" cy="6" r="5" fill="none" stroke="#d3161b"/><path d="M6 3v3l2 1" stroke="#d3161b" fill="none"/></svg>Mon–Sun: 9:00am – 11:00pm</div>
  </div>
  <div class="contact-form">
    <span>Name</span><span>Email</span><span>Phone</span><span class="area">Message</span>
    <span class="btn btn-red" style="display:inline-block;height:auto;border:0;color:#fff">Send message</span>
  </div>
  <div class="socials"><i></i><i></i><i></i><i></i><i></i><i></i></div>
</section>

<section class="map">
  <div class="ph" style="inset:0" role="img" aria-label="Street map of the marina area"></div>
  <div class="map-pin"><svg width="14" height="18" viewBox="0 0 10 13"><path d="M5 0a4 4 0 014 4c0 3-4 9-4 9S1 7 1 4a4 4 0 014-4z" fill="#d3161b"/></svg><span>Vellora</span></div>
</section>

<footer>Thank you and welcome back!</footer>
</body>
</html>
```